Design eines Hausetiketts für traditionelles Weingut
Zielgruppe
Wir das Familienweingut Kestrahl in Gimbsheim/Rheinhessen sind ein traditionelles Weingut das seine Reben selbst kultiviert und die Weine auch selbst ausbaut. Wir haben jeden Schritt in der Weinherstellung selbst in der Hand und vermarkten den Wein dann an unsere Privatkunden. Unsere Kundenstruktur sieht folgendermaßen aus: Wir haben 100% Privatkunden die unseren Wein konsumieren. Da jetzt die nächste Generation in den Weinbaubetrieb einsteigt und auch Ideen hat möchten wir ein Hausetikett einführen. Im Moment haben wir noch sehr viele unterschiedliche Etiketten und kein Hausetikett. Da die Verlagsetiketten immer seltener zu unseren Vorstellungen passen, möchten wir hier auf diesem Wege ein Hausetikett anfertigen lassen. Generell möchten wir unseren Außenauftritt komplett modernisieren. Sie können sich über die Vielfalt in unserem Betrieb unter www.weingut-kestrahl-beispiel.de einen Überblick verschaffen. Langfristig gesehen wollen wir aber unsere Weinkarte verkleinern.
Aufgabenstellung
Wir haben uns vor ca. 1,5 Jahren hier auf dieser Website bereits ein Logo designen lassen. Es wäre schön wenn man das Logo bei den Entwürfen für die Etiketten berücksichtigen würde. Das wäre aber KEIN MUSS. Auch wäre es gut wenn man das ,,Wein' bei unserem Namen weglassen könnte.
Das Etikett sollte aus Vorder-und Rückenetikett bestehen und edel wirken. Vorne sollte die Rebsorte und die Geschmacksangabe stehen. Der Rest sollte auf das Rückenetikett.
Das Vorderetikett sollte ein richtiger Eyecatcher sein und im Supermarkt z.B. aus vielen anderen herausstechen. Das wäre ganz wichtig.
Man kann bei den Farben unterscheiden in 3 Konzepte.
Literwein als einsteiger Wein
Dann die Gutsweine und zum Schluss die Lagenweine. Alles Farblich oder im design etwas abgesetzt.

```html
<!DOCTYPE html>
<html lang="de">
<head>
<meta charset="utf-8">
<title>Kestrahl – Hausetikett</title>
<link rel="stylesheet" href="https://fonts.googleapis.com/css2?family=Sacramento&family=Poiret+One&display=swap">
<style>
  :root {
    --paper: #ffffff;
    --ink: #000000;
    --band-red: #ff0000;
    --band-edge: #5a0000;
    --mark-red: #de2229;
  }
  html, body {
    margin: 0;
    padding: 0;
    width: 928px;
    height: 1200px;
    overflow: hidden;
    background: var(--paper);
  }
  .label {
    position: relative;
    width: 928px;
    height: 1200px;
    overflow: hidden;
    background: var(--paper);
    color: var(--ink);
  }
  .label__name {
    position: absolute;
    left: -4px;
    top: 200px;
    margin: 0;
    font-family: "Sacramento", cursive;
    font-weight: 400;
    font-size: 330px;
    line-height: 1;
    white-space: nowrap;
    letter-spacing: 2px;
  }
  .label__variety {
    position: absolute;
    left: 92px;
    top: 884px;
    margin: 0;
    font-family: "Poiret One", sans-serif;
    font-weight: 400;
    font-size: 75px;
    line-height: 1;
    white-space: nowrap;
  }
  .label__taste {
    position: absolute;
    left: 92px;
    top: 988px;
    margin: 0;
    font-family: "Poiret One", sans-serif;
    font-weight: 400;
    font-size: 44px;
    line-height: 1;
  }
  .band {
    position: absolute;
    top: 1107px;
    height: 25px;
    background: var(--band-red);
    box-sizing: border-box;
    border: 1px solid var(--band-edge);
  }
  .band--left { left: 0; width: 657px; }
  .band--right { left: 822px; width: 106px; }
  .house-mark {
    position: absolute;
    left: 664px;
    top: 970px;
    width: 153px;
    display: flex;
    flex-direction: column;
    align-items: center;
    gap: 18px;
  }
  .house-mark__name {
    font-family: "Poiret One", sans-serif;
    font-size: 30px;
    line-height: 1;
    color: var(--ink);
  }
  .house-mark__dot {
    width: 84px;
    height: 84px;
    border-radius: 50%;
    background: var(--mark-red);
  }
</style>
</head>
<body>
  <main class="label">
    <h1 class="label__name">Kestrahl</h1>
    <p class="label__variety">Rebsorte 2019</p>
    <p class="label__taste">fruchtig</p>
    <div class="band band--left"></div>
    <div class="band band--right"></div>
    <div class="house-mark">
      <span class="house-mark__name">Kestrahl</span>
      <span class="house-mark__dot"></span>
    </div>
  </main>
</body>
</html>
```